Corvane Business Cards

Front of business card will have logo, name, address, & telephone number. Back of card will have a list of services provided - Roads, Substation Pads, Temporary Pads, Site Pads, Land Leveling, Powerline Row Cleaning, Land Clearing, Gates, Fencing, Construction Entrances, Excavation, Trenching, Underground Utilities, Directional Boring, Pile Driving. We are a construction company that uses heavy equipment like bulldozers, motor graders/blades, dump trucks, backhoes, hydro axes, & skid loaders. We build roads, pads, & install electric utility lines & waterlines underground. This logo is new. The word "Construction" can be smaller as uploaded 2 example edited logos. We will be using this card design for many employees.
Target Market(s)
Industrial Electric Powerline, Wind Turbine, Solar Panel, & Water Utility companies.
Contact Information for Business Card
Name/Position - Dwayne Halster - Owner
Address: 4875 FM 309
Merkel, TX 79412
Phone number - (325) 482-5096

```html
<!DOCTYPE html>
<html lang="en">
<head>
<meta charset="utf-8">
<title>Corvane Business Cards</title>
<link rel="stylesheet" href="https://fonts.googleapis.com/css2?family=Marcellus&family=Montserrat:wght@400&family=Poppins:wght@400;600&display=swap">
<style>
  :root {
    --maroon: #3a0b16;
    --panel: #f3f3f3;
    --card-back: #e9e9e9;
    --ink-light: #ffffff;
    --ink-grey: #5a5a5a;
    --stage: #dcdcdc;
  }
  * { margin: 0; padding: 0; box-sizing: border-box; }
  html, body { width: 1125px; height: 1200px; overflow: hidden; }
  body { background: var(--stage); position: relative; }

  .card {
    position: absolute;
    left: 150px;
    width: 825px;
    height: 470px;
    border-radius: 24px;
    overflow: hidden;
    box-shadow: 0 6px 14px rgba(0,0,0,0.35);
  }
  .card--front { top: 98px; background: var(--maroon); }
  .card--back { top: 632px; background: radial-gradient(ellipse at 50% 40%, #f2f2f2, var(--card-back)); }

  .front-panel { position: absolute; inset: 0; width: 100%; height: 100%; }

  .identity { position: absolute; left: 51px; top: 52px; color: var(--ink-light); font-family: "Marcellus", serif; }
  .identity__name { font-weight: 400; font-size: 27px; letter-spacing: 1.5px; -webkit-text-stroke: 0.6px var(--ink-light); }
  .identity__role { font-size: 20px; margin-top: 0; letter-spacing: 0.5px; }

  .contact { position: absolute; left: 51px; top: 285px; color: var(--ink-light); font-family: "Montserrat", sans-serif; font-size: 19px; line-height: 23px; }
  .contact__address { margin-bottom: 10px; }
  .contact__row { display: flex; align-items: center; gap: 10px; }
  .contact__icon { width: 15px; height: 15px; flex: none; }

  .wordmark { position: absolute; text-align: center; color: var(--maroon); }
  .wordmark--front { left: 455px; top: 188px; width: 320px; }
  .wordmark--front .wordmark__name { font-family: "Poppins", sans-serif; font-weight: 600; font-size: 62px; line-height: 1; letter-spacing: 1px; }
  .wordmark--front .wordmark__sub { font-family: "Marcellus", serif; font-size: 30px; letter-spacing: 0.5px; margin-top: 16px; -webkit-text-stroke: 0.6px var(--maroon); }
  .wordmark--back { left: 0; top: 160px; width: 100%; }
  .wordmark--back .wordmark__name { font-family: "Poppins", sans-serif; font-weight: 600; font-size: 96px; line-height: 1; letter-spacing: 2px; }

  .services { position: absolute; left: 0; top: 376px; width: 100%; text-align: center; font-family: "Poppins", sans-serif; font-size: 18px; line-height: 22px; color: var(--ink-grey); }
  .services li { list-style: none; display: inline; }
  .services li + li::before { content: "\2022"; margin: 0 4px; }
  .services__line { display: block; }
</style>
</head>
<body>

<section class="card card--front" aria-label="Card front">
  <svg class="front-panel" viewBox="0 0 825 470" preserveAspectRatio="none" aria-hidden="true">
    <path fill="#f3f3f3" d="M465 0 H825 V470 H410 C440 440 455 390 435 360 C420 345 405 340 385 345 C330 350 290 290 288 225 C286 160 320 115 345 112 C365 110 395 130 420 120 C450 105 440 60 425 40 C415 20 430 5 465 0 Z"/>
  </svg>

  <div class="identity">
    <h1 class="identity__name">DWAYNE HALSTER</h1>
    <p class="identity__role">Owner</p>
  </div>

  <div class="contact">
    <p class="contact__address">4875 FM 309<br>Dunmoor, TX 79412</p>
    <p class="contact__row">
      <svg class="contact__icon" viewBox="0 0 16 16"><path fill="#fff" d="M3.6 1.2l2.3 2.6-1.3 1.8c.8 1.9 2.2 3.3 4 4.1l1.8-1.3 2.7 2.3-1.2 2.3C7.2 12.7 3.3 8.8 1.3 3z"/></svg>
      (555) 482-5096
    </p>
    <p class="contact__row">
      <svg class="contact__icon" viewBox="0 0 16 16"><rect x="1.5" y="4" width="13" height="8.5" fill="#fff"/><path d="M1.5 4.5l6.5 4.5 6.5-4.5" stroke="#3a0b16" stroke-width="1.2" fill="none"/></svg>
      info@corvaneconstruction.com
    </p>
    <p class="contact__row">
      <svg class="contact__icon" viewBox="0 0 16 16"><circle cx="8" cy="8" r="7" fill="#fff"/><path d="M5 4c2 1 1 3 3 3s1 3 3 2M4 10c1 0 2 1 2 3" stroke="#3a0b16" stroke-width="1.2" fill="none"/></svg>
      corvaneconstruction.com
    </p>
  </div>

  <div class="wordmark wordmark--front">
    <p class="wordmark__name">CORVANE</p>
    <p class="wordmark__sub">CONSTRUCTION</p>
  </div>
</section>

<section class="card card--back" aria-label="Card back">
  <div class="wordmark wordmark--back">
    <p class="wordmark__name">CORVANE</p>
  </div>

  <div class="services">
    <ul class="services__line"><li>Roads</li><li>Substation Pads</li><li>Temporary Pads</li><li>Site Pads</li><li>Land Leveling</li></ul>
    <ul class="services__line"><li>Powerline Row Cleaning</li><li>Land Clearing</li><li>Gates</li><li>Fencing</li><li>Construction Entrances</li></ul>
    <ul class="services__line"><li>Excavation</li><li>Trenching</li><li>Underground Utilities</li><li>Directional Boring</li><li>Pile Driving</li></ul>
  </div>
</section>

</body>
</html>
```